PowerPoint Re-Design and Template Needs a Designer's Eye!

I have the text, images and logo for a PowerPoint but need your Design and Template skills! Less than 20 pages, needs to be concise, include images, must have creative page layouts, include our floater-logo on every page, use sidebars or call-outs for important information, have color but not too much because this will be printed many times (our current colors are too dark). You can use bullet-points or paragraphs. You can also change the titles, font, color, layout - anything! This is YOUR PowerPoint to create the most impressive Template! We are an investment management firm located in New York City. Our investment returns are the very best in the industry and we want this PowerPoint to convey our "best in class" style.

Notes:
1) Please use the PPP outline attached.
2) I have attached a rough draft PPP. Please use the logos on page 2. Some pages do not have text, the final text will be available shortly.
3) I have attached examples you can reference.
4) Please include our floater-logo on every page.
5) Please feel free to ask questions or clarification.

Hi Designers, Thank you very much for your wonderful submissions! My partners and I are going through each submission in detail today and tomorrow. We'll be in touch over the next few days with additional questions and comments. Stay tuned! Best, Damon Quillfeather

High-net worth individuals and institutions. New York City, Wall Street.

Investment

• - Floater-logo on every page
- Sidebars or call-outs on several pages (you can decide which ones)
- Please include images; however, the PPP Template is the most important.

```html
<!DOCTYPE html>
<html lang="en">
<head>
<meta charset="utf-8">
<title>Table of Contents</title>
<link rel="stylesheet" href="https://fonts.googleapis.com/css2?family=Arimo:wght@700&family=Questrial&family=Archivo+Narrow:wght@400&display=swap">
<style>
  :root {
    --orange: #f57c00;
    --ink: #111111;
    --muted: #6b6b6b;
    --rule: #b9b9b9;
    --footer: #6e6e6e;
    --white: #ffffff;
  }
  * { box-sizing: border-box; margin: 0; padding: 0; }
  html, body { width: 1200px; height: 900px; overflow: hidden; background: var(--white); }
  .slide { position: relative; width: 1200px; height: 900px; background: var(--white); }

  .header {
    position: absolute; left: 0; top: 0; width: 1200px; height: 93px;
    background: var(--orange);
  }
  .header__rule {
    position: absolute; left: 0; top: 97px; width: 1200px; height: 2px;
    background: var(--rule);
  }
  .header__title {
    position: absolute; left: 27px; top: 28px;
    font-family: "Arimo", Arial, sans-serif; font-weight: 700;
    font-size: 34px; line-height: 40px; color: var(--ink); letter-spacing: -0.3px;
  }
  .brand {
    position: absolute; right: 22px; top: 16px; height: 62px;
    display: flex; align-items: center; gap: 10px;
  }
  .brand__dot { width: 26px; height: 26px; border-radius: 50%; background: var(--white); }
  .brand__name {
    font-family: "Questrial", sans-serif; font-size: 26px; color: var(--white);
  }

  .contents { position: absolute; left: 87px; top: 171px; width: 1076px; list-style: none; }
  .contents__item { display: flex; height: 72px; margin-bottom: 19.5px; }
  .contents__num {
    width: 93px; height: 72px; background: var(--orange); color: var(--white);
    font-family: "Arimo", Arial, sans-serif; font-weight: 700; font-size: 36px;
    display: flex; align-items: center; justify-content: center;
  }
  .contents__label {
    margin-left: 6px; flex: 1; height: 72px;
    border: 1.5px solid var(--orange);
    display: flex; align-items: center; padding-left: 21px;
    font-family: "Questrial", sans-serif; font-size: 31px; color: var(--muted);
  }

  .footer {
    position: absolute; left: 0; top: 860px; width: 1200px; height: 40px;
    background: var(--footer); color: var(--white);
    font-family: "Archivo Narrow", "Arial Narrow", sans-serif; font-size: 18px;
    display: flex; align-items: center; justify-content: space-between;
    padding: 0 9px 0 8px;
  }
</style>
</head>
<body>
  <div class="slide">
    <header class="header">
      <h1 class="header__title">TABLE OF CONTENTS</h1>
      <div class="brand">
        <span class="brand__dot"></span>
        <span class="brand__name">Halvern</span>
      </div>
    </header>
    <div class="header__rule"></div>

    <ol class="contents">
      <li class="contents__item"><span class="contents__num">01</span><span class="contents__label">Investment Highlights</span></li>
      <li class="contents__item"><span class="contents__num">02</span><span class="contents__label">Investment Strategy Overview</span></li>
      <li class="contents__item"><span class="contents__num">03</span><span class="contents__label">Investment Strategy Process</span></li>
      <li class="contents__item"><span class="contents__num">04</span><span class="contents__label">Investment Strategy Analysis</span></li>
      <li class="contents__item"><span class="contents__num">05</span><span class="contents__label">Service Providers</span></li>
    </ol>

    <footer class="footer">
      <span class="footer__author">Damon Quillfeather 2015</span>
      <span class="footer__page">Page : 01</span>
    </footer>
  </div>
</body>
</html>
```